Business Card Design for company

We want new business cards. We'd like something different-- yet still highly professional. Our tagline is Providing leadership, delivering success. Stock photos are ok, as long as they are relevant and look upscale.

Target Market(s)

Architecture/Business Management Consulting/Engineering Consulting

Contact Information for Business Card

dark gray background with pops of blue might be good, but you tell me. You're the designers. Rounded corners might be nice, but again, you tell me.

Font styles to use
Serif
Sans Serif

Colors
3276b5
5c5c5c
9d9d9d
fbfbfb

Requirements
Nice to have
• Something different, but still very professional.

```html
<!DOCTYPE html>
<html lang="en">
<head>
<meta charset="utf-8">
<title>Veltora Partners – Business Cards</title>
<link rel="stylesheet" href="https://fonts.googleapis.com/css2?family=Montserrat:wght@400;500;700&display=swap">
<style>
  :root {
    --brand-blue: #3276b5;
    --brand-blue-light: #4a8ac6;
    --card-white: #fbfbfb;
    --stage: #262626;
    --text-white: #ffffff;
    --divider: rgba(255,255,255,0.55);
  }
  * { margin: 0; padding: 0; box-sizing: border-box; }
  html, body { width: 1200px; height: 900px; overflow: hidden; }
  body {
    background: var(--stage);
    font-family: "Montserrat", Arial, sans-serif;
    color: var(--text-white);
    position: relative;
  }
  .card {
    position: absolute;
    left: 290px;
    width: 620px;
    height: 354px;
    background: var(--brand-blue);
    overflow: hidden;
    box-shadow: 0 12px 30px rgba(0,0,0,0.45);
  }
  .card--front { top: 56px; }
  .card--back { top: 450px; }

  /* Front */
  .world-map-area {
    position: absolute;
    left: 30px; top: 22px;
    width: 560px; height: 270px;
    border-radius: 40px;
    background: radial-gradient(ellipse at center, var(--brand-blue-light) 0%, rgba(74,138,198,0.35) 55%, rgba(50,118,181,0) 80%);
  }
  .front-lockup {
    position: absolute;
    left: 0; right: 0; top: 108px;
    text-align: center;
  }
  .brand-name {
    font-weight: 500;
    color: var(--text-white);
    line-height: 1;
  }
  .front-lockup .brand-name--main { font-size: 74px; letter-spacing: 4px; }
  .front-lockup .brand-name--sub { font-size: 28px; letter-spacing: 5px; margin-top: 8px; }
  .tagline {
    position: absolute;
    left: 0; right: 0; top: 282px;
    text-align: center;
    font-size: 12px;
    letter-spacing: 2px;
    font-weight: 500;
  }

  /* Back */
  .back-lockup {
    position: absolute;
    left: 40px; top: 118px;
    width: 280px;
    text-align: center;
  }
  .back-lockup .brand-name--main { font-size: 54px; letter-spacing: 3px; }
  .back-lockup .brand-name--sub { font-size: 20px; letter-spacing: 4px; margin-top: 8px; }
  .back-divider {
    position: absolute;
    left: 340px; top: 58px;
    width: 1px; height: 150px;
    background: var(--divider);
  }
  .contact-block {
    position: absolute;
    left: 362px; top: 52px;
  }
  .person-name { font-size: 19px; font-weight: 700; letter-spacing: 1px; }
  .person-title { font-size: 12.5px; font-weight: 500; margin-top: 2px; margin-bottom: 14px; }
  .contact-list { list-style: none; font-size: 12.5px; }
  .contact-list li { display: flex; align-items: center; gap: 10px; height: 19px; }
  .contact-icon { width: 11px; height: 11px; flex: none; }
  .address-band {
    position: absolute;
    left: 0; right: 0; bottom: 0;
    height: 58px;
    background: var(--card-white);
    border-top: 3px solid var(--card-white);
  }
  .address-band::before {
    content: "";
    position: absolute;
    left: 0; right: 0; top: -10px;
    height: 3px;
    background: var(--card-white);
  }
  .address {
    position: absolute;
    left: 0; right: 0; top: 16px;
    text-align: center;
    font-size: 13px;
    color: var(--brand-blue);
    font-weight: 500;
  }
</style>
</head>
<body>

<section class="card card--front">
  <div class="world-map-area" role="img" aria-label="Faint dotted world map spread across the card"></div>
  <div class="front-lockup">
    <div class="brand-name brand-name--main">VELTORA</div>
    <div class="brand-name brand-name--sub">PARTNERS</div>
  </div>
  <p class="tagline">GUIDING STRATEGY | BUILDING LASTING RESULTS</p>
</section>

<section class="card card--back">
  <div class="back-lockup">
    <div class="brand-name brand-name--main">VELTORA</div>
    <div class="brand-name brand-name--sub">PARTNERS</div>
  </div>
  <div class="back-divider"></div>
  <div class="contact-block">
    <p class="person-name">DANIEL HARTWELL</p>
    <p class="person-title">Design Consultant</p>
    <ul class="contact-list">
      <li>
        <svg class="contact-icon" viewBox="0 0 12 12"><rect x="3" y="0.5" width="6" height="11" rx="1" fill="none" stroke="#fff" stroke-width="1.2"/><circle cx="6" cy="9.5" r="0.7" fill="#fff"/></svg>
        555-014-2290
      </li>
      <li>
        <svg class="contact-icon" viewBox="0 0 12 12"><path d="M2.5 1 L4.5 1 L5.3 3.6 L4 4.6 Q5 7 7.4 8 L8.4 6.7 L11 7.5 L11 9.5 Q11 11 9.5 11 Q1 10 1 2.5 Q1 1 2.5 1Z" fill="#fff"/></svg>
        01632 960418 (Northgate)
      </li>
      <li>
        <svg class="contact-icon" viewBox="0 0 12 12"><path d="M2.5 1 L4.5 1 L5.3 3.6 L4 4.6 Q5 7 7.4 8 L8.4 6.7 L11 7.5 L11 9.5 Q11 11 9.5 11 Q1 10 1 2.5 Q1 1 2.5 1Z" fill="#fff"/></svg>
        01632 960577 (Eastfield)
      </li>
      <li>
        <svg class="contact-icon" viewBox="0 0 12 12"><rect x="0.6" y="2.2" width="10.8" height="7.6" fill="none" stroke="#fff" stroke-width="1.2"/><path d="M0.8 2.6 L6 6.6 L11.2 2.6" fill="none" stroke="#fff" stroke-width="1.2"/></svg>
        info@veltorapartners
      </li>
      <li>
        <svg class="contact-icon" viewBox="0 0 12 12"><circle cx="6" cy="6" r="5" fill="none" stroke="#fff" stroke-width="1.1"/><ellipse cx="6" cy="6" rx="2.2" ry="5" fill="none" stroke="#fff" stroke-width="0.9"/><path d="M1 6 H11" stroke="#fff" stroke-width="0.9"/></svg>
        www.veltorapartners.com
      </li>
    </ul>
  </div>
  <div class="address-band">
    <p class="address">Suite 14, The Marlow Centre, Ashby Park, Northgate, Westmere NG4 2QT</p>
  </div>
</section>

</body>
</html>
```